Cool business cards

Use my existing logo from mark meadow (see images I have uploaded) and design a really cool non-stuffy business card. I am a divorce mediator.

```html
<!DOCTYPE html>
<html lang="en">
<head>
<meta charset="utf-8">
<title>Mark Meadow, J.D. — Business Card</title>
<link rel="stylesheet" href="https://fonts.googleapis.com/css2?family=Montserrat:wght@300;400;600;700&display=swap">
<style>
  :root {
    --stage: #000000;
    --brand-blue: #0b66ae;
    --brand-orange: #f0821e;
    --paper: #ffffff;
    --muted: #8c8c8c;
    --muted-light: #c9ced6;
  }
  * { margin: 0; padding: 0; box-sizing: border-box; }
  html, body { width: 1200px; height: 993px; overflow: hidden; background: var(--stage); }
  body { position: relative; font-family: "Montserrat", sans-serif; }

  .card { position: absolute; left: 246px; width: 686px; height: 392px; }
  .card--front { top: 80px; background: var(--brand-blue); }
  .card--back { top: 511px; background: var(--paper); }

  .lockup { position: absolute; display: flex; flex-direction: column; align-items: center; }
  .lockup__disc { border-radius: 50%; }
  .lockup__name { font-weight: 700; letter-spacing: 0.5px; white-space: nowrap; }
  .lockup__tagline {
    display: flex; align-items: center; font-weight: 600; letter-spacing: 0.6px;
    white-space: nowrap; color: var(--muted-light);
  }
  .lockup__tagline::before, .lockup__tagline::after {
    content: ""; display: block; height: 1.5px; background: currentColor;
  }

  .card--front .lockup { left: 0; right: 0; top: 95px; }
  .card--front .lockup__disc { width: 124px; height: 124px; background: var(--brand-orange); }
  .card--front .lockup__name { margin-top: 25px; font-size: 28px; color: var(--paper); }
  .card--front .lockup__tagline { margin-top: 2px; font-size: 12.5px; }
  .card--front .lockup__tagline::before, .card--front .lockup__tagline::after { width: 24px; margin: 0 8px; }

  .card--back .lockup { left: 40px; width: 270px; top: 121px; }
  .card--back .lockup__disc { width: 96px; height: 96px; background: var(--brand-blue); }
  .card--back .lockup__name { margin-top: 17px; font-size: 20.5px; color: var(--brand-blue); }
  .card--back .lockup__tagline { margin-top: 1px; font-size: 9.5px; color: var(--muted); }
  .card--back .lockup__tagline::before, .card--back .lockup__tagline::after { width: 19px; margin: 0 7px; }

  .holder-name {
    position: absolute; left: 354px; top: 54px;
    font-size: 20px; font-weight: 400; color: var(--muted); letter-spacing: 0.5px;
  }
  .contact { position: absolute; left: 351px; top: 216px; list-style: none; }
  .contact__item {
    display: flex; align-items: center; height: 41px;
    font-size: 20px; font-weight: 300; color: var(--muted);
  }
  .contact__icon { width: 24px; height: 24px; margin-right: 9px; fill: var(--muted); }
</style>
</head>
<body>
  <section class="card card--front">
    <div class="lockup">
      <div class="lockup__disc"></div>
      <div class="lockup__name">MARK MEADOW, J.D.</div>
      <div class="lockup__tagline">DIVORCE &amp; FAMILY MEDIATION</div>
    </div>
  </section>

  <section class="card card--back">
    <div class="lockup">
      <div class="lockup__disc"></div>
      <div class="lockup__name">MARK MEADOW, J.D.</div>
      <div class="lockup__tagline">DIVORCE &amp; FAMILY MEDIATION</div>
    </div>

    <p class="holder-name">NAME</p>

    <ul class="contact">
      <li class="contact__item">
        <svg class="contact__icon" viewBox="0 0 24 24" aria-hidden="true"><path d="M6.6 3.5 9 3l1.6 4.2-1.7 1.6a11 11 0 0 0 6.3 6.3l1.6-1.7L21 15l-.5 2.4c-.3 1.4-1.6 2.3-3 2.1C10.4 18.6 5.4 13.6 4.5 6.5c-.2-1.4.7-2.7 2.1-3Z"/></svg>
        +00 000000000
      </li>
      <li class="contact__item">
        <svg class="contact__icon" viewBox="0 0 24 24" aria-hidden="true"><path d="M2 6h20v12H2Z" fill="none" stroke="#8c8c8c" stroke-width="0"/><path d="M2 6h20l-10 7Z"/><path d="M2 8l10 7 10-7v10H2Z"/></svg>
        name@markmeadow.com
      </li>
      <li class="contact__item">
        <svg class="contact__icon" viewBox="0 0 24 24" aria-hidden="true" fill="none" stroke="#8c8c8c" stroke-width="1.6"><circle cx="12" cy="12" r="10"/><ellipse cx="12" cy="12" rx="4.5" ry="10"/><path d="M2 12h20M4 7h16M4 17h16"/></svg>
        www.markmeadow.com
      </li>
    </ul>
  </section>
</body>
</html>
```